Agriculture Business Card

I want to use my existing logo and use my tagline of "Don't Guess...Soil Test" on the card. Looking for a double sided card that will really get peoples attention.
Contact Info:
Marlow Field Crop Edge
Calvin Brusk
2917 K Lane
Larkin, NE 68593
402-555-0193
calvin.r.brusk@fieldmailbox.net

```html
<!DOCTYPE html>
<html lang="en">
<head>
<meta charset="utf-8">
<title>Marlow Field Crop Edge – Business Card</title>
<link rel="stylesheet" href="https://fonts.googleapis.com/css2?family=Fira+Sans+Condensed:wght@700&family=Fira+Sans:wght@800&family=Arimo:wght@400;700&display=swap">
<style>
  :root {
    --backdrop: #c9c9c9;
    --soil: #a0694b;
    --soil-dark: #8a573c;
    --paper: #ffffff;
    --ink: #1f1f1f;
    --brand-brown: #8c5a3c;
    --label-brown: #a8714f;
    --leaf-green: #3aa629;
    --gold: #f6b01a;
  }
  * { margin: 0; padding: 0; box-sizing: border-box; }
  html, body {
    width: 1200px; height: 900px; overflow: hidden;
    background: var(--backdrop);
  }
  .sheet { position: relative; width: 1200px; height: 900px; }
  .card {
    position: absolute; left: 250px; width: 700px; height: 400px;
    border-radius: 26px; overflow: hidden;
  }
  .card--front { top: 35px; background: var(--soil); }
  .card--back { top: 465px; background: var(--paper); }

  .brand {
    display: flex; align-items: center; gap: 16px;
    font-family: "Fira Sans Condensed", sans-serif; font-weight: 700;
    line-height: 1.0;
  }
  .brand__dot { width: 64px; height: 64px; border-radius: 50%; background: var(--gold); flex: none; }
  .brand__name { font-size: 34px; }

  .card--front .brand {
    position: absolute; left: 50%; top: 50%; transform: translate(-50%, -50%);
    color: var(--paper);
  }
  .card--back .brand {
    position: absolute; left: 60px; top: 70px; color: var(--brand-brown);
  }

  .contact {
    position: absolute; left: 60px; top: 200px;
    font-family: Arimo, sans-serif; color: var(--ink);
  }
  .contact__name {
    font-family: "Fira Sans", sans-serif; font-weight: 800;
    font-size: 34px; color: var(--brand-brown); margin-bottom: 10px;
  }
  .contact__line { display: flex; align-items: center; gap: 10px; font-size: 20px; line-height: 1.35; }
  .contact__icon { width: 18px; height: 18px; fill: var(--brand-brown); flex: none; }
  .contact__company { margin-top: 16px; font-size: 21px; color: var(--label-brown); line-height: 1.3; }
  .contact__address { font-size: 21px; line-height: 1.3; }

  .tagline {
    position: absolute; right: 46px; bottom: 70px;
    font-family: Arimo, sans-serif; font-weight: 700; font-size: 20px;
    color: var(--leaf-green); letter-spacing: 0.5px; text-transform: uppercase;
  }
</style>
</head>
<body>
<main class="sheet">
  <section class="card card--front" aria-label="Card front">
    <div class="brand">
      <span class="brand__dot"></span>
      <span class="brand__name">Marlow Field Crop Edge</span>
    </div>
  </section>

  <section class="card card--back" aria-label="Card back">
    <div class="brand">
      <span class="brand__dot"></span>
      <span class="brand__name">Marlow Field Crop Edge</span>
    </div>

    <div class="contact">
      <h1 class="contact__name">Calvin Brusk</h1>
      <p class="contact__line">
        <svg class="contact__icon" viewBox="0 0 24 24" aria-hidden="true"><path d="M6.6 10.8a15.1 15.1 0 0 0 6.6 6.6l2.2-2.2a1 1 0 0 1 1-.25 11.4 11.4 0 0 0 3.6.57 1 1 0 0 1 1 1V20a1 1 0 0 1-1 1A17 17 0 0 1 3 4a1 1 0 0 1 1-1h3.5a1 1 0 0 1 1 1c0 1.25.2 2.45.57 3.57a1 1 0 0 1-.25 1z"/></svg>
        402-555-0193
      </p>
      <p class="contact__line">
        <svg class="contact__icon" viewBox="0 0 24 24" aria-hidden="true"><path d="M2 5h20v14H2z M2 5l10 8 10-8" fill="none" stroke="#8c5a3c" stroke-width="2"/></svg>
        calvin.r.brusk@fieldmailbox.net
      </p>
      <p class="contact__company">Marlow Field Crop Edge</p>
      <p class="contact__address">2917 K Lane, Larkin, NE 68593</p>
    </div>

    <p class="tagline">Don't Guess...Soil Test</p>
  </section>
</main>
</body>
</html>
```